Fresh Dwelling Tract Guide needs a new Landing Page

I like to get a landing page or website with 2-3 pages to help target home buyers who are looking to buy homes from builders such as TW Residences, Morvik, P.L. Fennick, etc. The landing page/website to be non-cluttered and be able to explain to home buyers that there are many benefits to include me as their buyer's agent when they buy a brand new home from any builders.
I may want to incorporate a short explanation video (animated) on the landing page and then for the viewer to click on a button that will take them to another page where they can search for new homes from different builders.
Target Market(s)
Home buyers looking to buy brand new home from builders such as TW Residences, Morvik, P.L. Fennick, etc.
Industry/Entity Type
Real Estate
Number of Pages Required
2 page
Font styles to use
Requirements
Must have
- The landing page may have the explanation video at the bottom of the landing page (scrolled down) or there may be a CALL TO ACTION button that takes the viewer to the 2nd page to watch the explanation video. Once they watched the explanation video and are still interested, they can click on another CALL TO ACTION button that will take them to another website that they will be able to search for all the available new homes and register their contact information.
Should not have
- No clutters and no dark colors.

```html
<!DOCTYPE html>
<html lang="en">
<head>
<meta charset="utf-8">
<title>Fresh Dwelling Tract Guide — Blog &amp; Success Stories</title>
<link rel="stylesheet" href="https://fonts.googleapis.com/css2?family=Lora:ital,wght@0,400;1,400&family=Open+Sans:wght@400;700&display=swap">
<style>
  :root {
    --ink: #5b4630;
    --ink-soft: #5f5246;
    --link: #4a8fd6;
    --accent: #a6b943;
    --panel: #f4f4f4;
    --white: #ffffff;
    --sky: #52c6df;
    --roof: #e08a9a;
    --park: #4e6b3a;
    --portrait: #8a8a8a;
  }
  * { box-sizing: border-box; margin: 0; padding: 0; }
  html, body { width: 1200px; height: 1200px; overflow: hidden; background: var(--white); }
  body { position: relative; font-family: "Open Sans", sans-serif; color: var(--ink); }

  .section-label { position: absolute; left: 88px; top: 34px; font-family: "Lora", serif; font-size: 22px; letter-spacing: 0.5px; color: var(--ink); }

  .post { position: absolute; top: 130px; width: 489px; }
  .post--left { left: 87px; }
  .post--right { left: 624px; }
  .post__media { width: 489px; height: 292px; box-shadow: 0 2px 5px rgba(0,0,0,0.15); }
  .post__media--gable { background: linear-gradient(160deg, var(--sky) 0%, var(--sky) 45%, var(--roof) 46%, #d97e8e 100%); }
  .post__media--park { background: linear-gradient(135deg, #e8dcc0 0%, var(--park) 35%, #efe4c8 60%, #3f5a2f 100%); }
  .post__title { margin-top: 20px; font-family: "Lora", serif; font-size: 23px; font-weight: 400; color: var(--ink); line-height: 1.2; }
  .post__meta { margin-top: 16px; font-size: 9px; text-transform: uppercase; color: var(--ink-soft); }
  .post__meta a { color: var(--link); text-decoration: none; }
  .post__meta .sep { color: #b5aba0; margin: 0 3px; }
  .post__excerpt { margin-top: 22px; font-size: 14.5px; line-height: 21px; color: var(--ink-soft); }
  .post__more { display: inline-block; margin-top: 16px; font-size: 14.5px; color: var(--link); text-decoration: none; }

  .view-more { position: absolute; left: 509px; top: 667px; width: 182px; height: 54px; background: var(--accent); color: var(--white); font-weight: 700; font-size: 14px; letter-spacing: 1.6px; display: flex; align-items: center; justify-content: center; border-radius: 2px; }

  .stories { position: absolute; left: 0; top: 788px; width: 1200px; height: 412px; background: var(--panel); }
  .stories__title { position: absolute; top: 86px; width: 100%; text-align: center; font-family: "Lora", serif; font-weight: 400; font-size: 34px; color: var(--ink); }
  .stories__portrait { position: absolute; left: 175px; top: 152px; width: 172px; height: 172px; border-radius: 50%; background: radial-gradient(circle at 55% 45%, #c8c8c8, var(--portrait) 60%, #3c3c3c); box-shadow: 0 2px 4px rgba(0,0,0,0.15); }
  .stories__arrow { position: absolute; top: 222px; }
  .stories__arrow--prev { left: 84px; }
  .stories__arrow--next { left: 1094px; }
  .stories__mark { position: absolute; left: 436px; top: 170px; font-family: "Lora", serif; font-size: 70px; line-height: 1; color: var(--ink); }
  .stories__quote { position: absolute; left: 433px; top: 250px; width: 600px; font-family: "Lora", serif; font-style: italic; font-size: 23px; line-height: 28px; color: var(--ink); }
  .stories__author { position: absolute; left: 433px; top: 336px; font-size: 14.5px; color: var(--ink-soft); }
  .stories__author strong { color: var(--ink); }
</style>
</head>
<body>
  <h2 class="section-label">BLOG</h2>

  <article class="post post--left">
    <div class="post__media post__media--gable" role="img" aria-label="Pink gabled house roof against a clear blue sky"></div>
    <h3 class="post__title">Open House Weekend Report: September 21-23</h3>
    <p class="post__meta">By TW Residences<span class="sep">|</span><a href="#">Homes</a><span class="sep">|</span>Sep 20</p>
    <p class="post__excerpt">Get up close and personal with Halvern during one of our favorite home tours in New York City, the Hamptons, and South Florida.</p>
    <a class="post__more" href="#">READ MORE</a>
  </article>

  <article class="post post--right">
    <div class="post__media post__media--park" role="img" aria-label="Aerial view of terraced homes with green rooftop gardens"></div>
    <h3 class="post__title">6 Homes with Incredible Park Views</h3>
    <p class="post__meta">By Morvik<span class="sep">|</span><a href="#">Homes</a><span class="sep">|</span>Sep 19</p>
    <p class="post__excerpt">There’s no better spot to watch the leaves change this foliage season than your own home!</p>
    <a class="post__more" href="#">READ MORE</a>
  </article>

  <a class="view-more">VIEW MORE</a>

  <section class="stories">
    <h2 class="stories__title">Success Stories</h2>
    <svg class="stories__arrow stories__arrow--prev" width="20" height="34" viewBox="0 0 20 34"><polyline points="17,2 3,17 17,32" fill="none" stroke="#a6b943" stroke-width="3"/></svg>
    <div class="stories__portrait" role="img" aria-label="Portrait of the client giving the testimonial"></div>
    <div class="stories__mark">“</div>
    <p class="stories__quote">Lorem ipsum dolor sit amet, consectetur adipisicing elit, sed do eiusmod</p>
    <p class="stories__author"><strong>Mara Quillen</strong>, VP of Global Marketing, Solvane</p>
    <svg class="stories__arrow stories__arrow--next" width="20" height="34" viewBox="0 0 20 34"><polyline points="3,2 17,17 3,32" fill="none" stroke="#a6b943" stroke-width="3"/></svg>
  </section>
</body>
</html>
```